Business Card Design for Occupational Medicine Start Up Company

We need to design a professional business card. We are a healthcare company providing occupational medicine services to blue collar industries. We are professional, efficient and high quality service providers.

Target Market(s)

Blue Collar Industry: Shipbuilding, Ports, Trucking Companies; The Executives and Safety Officers for these companies

Industry/Entity Type

Healthcare

Contact Information for Business Card

Logo, Name, Title, Email, Phone

Other font styles liked:
• Please match our Brand Guide

Requirements
Must have
• Our Company Colors and Logo

```html
<!DOCTYPE html>
<html lang="en">
<head>
<meta charset="utf-8">
<title>CrewCare Clinics – Business Card</title>
<link href="https://fonts.googleapis.com/css2?family=Montserrat:wght@400;500;700;800&display=swap" rel="stylesheet">
<style>
  :root {
    --navy: #2e3388;
    --sky: #29a8e0;
    --amber: #f3ae4b;
    --white: #ffffff;
    --stage: #e9eaee;
    --card-w: 520px;
    --card-h: 300px;
  }
  * { box-sizing: border-box; margin: 0; padding: 0; }
  html, body {
    width: 1200px; height: 913px; overflow: hidden;
    background: var(--stage);
    font-family: "Montserrat", Arial, sans-serif;
  }
  .sheet {
    width: 1200px; height: 913px;
    display: flex; align-items: center; justify-content: center; gap: 60px;
  }
  .card {
    position: relative;
    width: var(--card-w); height: var(--card-h);
    border-radius: 18px; overflow: hidden;
    box-shadow: 0 10px 30px rgba(20, 24, 60, 0.18);
  }

  /* Front */
  .card--front { background: var(--navy); }
  .front-brand {
    position: absolute; left: 0; right: 0; top: 50%;
    transform: translateY(-50%);
    display: flex; align-items: center; justify-content: center; gap: 18px;
  }
  .brand-dot {
    width: 58px; height: 58px; border-radius: 50%;
    background: var(--amber);
  }
  .front-brand .brand-name {
    color: var(--white);
    font-weight: 700; font-size: 34px; letter-spacing: 1px; line-height: 1.05;
  }
  .brand-name small {
    display: block; font-size: 0.42em; letter-spacing: 0.6em; margin-top: 4px;
  }

  /* Back */
  .card--back { background: var(--white); }
  .back-wave { position: absolute; inset: 0; }
  .back-brand {
    position: absolute; left: 70px; top: 48px;
    display: flex; align-items: center; gap: 14px;
  }
  .back-brand .brand-dot { width: 40px; height: 40px; }
  .back-brand .brand-name {
    color: var(--navy);
    font-weight: 700; font-size: 26px; letter-spacing: 1px; line-height: 1.05;
  }
  .holder {
    position: absolute; left: 96px; width: 210px; bottom: 30px; text-align: right;
  }
  .holder-name {
    color: var(--amber); font-weight: 800; font-size: 20px; letter-spacing: 0.5px;
    white-space: nowrap;
  }
  .holder-title {
    color: var(--white); font-weight: 400; font-size: 14px; margin-top: 2px;
  }
  .divider {
    position: absolute; left: 322px; bottom: 30px;
    width: 1.5px; height: 62px; background: var(--amber);
  }
  .contact {
    position: absolute; left: 338px; bottom: 32px;
    list-style: none; color: var(--white); font-size: 11px; line-height: 1.75;
    white-space: nowrap;
  }
  .contact li { display: flex; align-items: center; gap: 7px; }
  .contact svg { width: 11px; height: 11px; fill: var(--amber); flex: none; }
</style>
</head>
<body>
<main class="sheet">
  <section class="card card--front" aria-label="Card front">
    <div class="front-brand">
      <span class="brand-dot"></span>
      <span class="brand-name">CREWCARE<small>CLINICS</small></span>
    </div>
  </section>

  <section class="card card--back" aria-label="Card back">
    <svg class="back-wave" viewBox="0 0 520 300" preserveAspectRatio="none" aria-hidden="true">
      <path d="M120,222 C260,156 380,116 520,100" fill="none" stroke="var(--amber)" stroke-width="6"/>
      <path d="M0,276 C140,212 300,142 520,114" fill="none" stroke="var(--sky)" stroke-width="6"/>
      <path d="M0,300 L0,290 C150,222 310,152 520,124 L520,300 Z" fill="var(--navy)"/>
    </svg>

    <div class="back-brand">
      <span class="brand-dot"></span>
      <span class="brand-name">CREWCARE<small>CLINICS</small></span>
    </div>

    <div class="holder">
      <p class="holder-name">MARK DELANEY</p>
      <p class="holder-title">President</p>
    </div>

    <span class="divider"></span>

    <ul class="contact">
      <li>
        <svg viewBox="0 0 24 24"><path d="M6.6 10.8a15.1 15.1 0 0 0 6.6 6.6l2.2-2.2c.3-.3.7-.4 1-.2 1.1.4 2.3.6 3.6.6.6 0 1 .4 1 1V20c0 .6-.4 1-1 1A17 17 0 0 1 3 4c0-.6.4-1 1-1h3.5c.6 0 1 .4 1 1 0 1.3.2 2.5.6 3.6.1.3 0 .7-.2 1z"/></svg>
        555-310-4827
      </li>
      <li>
        <svg viewBox="0 0 24 24"><path d="M2 5h20v14H2z M2 5l10 8 10-8"/></svg>
        mark@crewcareclinics.com
      </li>
      <li>
        <svg viewBox="0 0 24 24"><circle cx="12" cy="12" r="10"/></svg>
        www.crewcareclinics.com
      </li>
    </ul>
  </section>
</main>
</body>
</html>
```